Building Referrer Relationships Booklet

4 page A4 booklet to give to potential professional referrers to establish a collaborative relationship.Needs to be bright, vibrant, colourful, friendly, inviting, in keeping with The Linden Practice colours.
Want to provide potential referrer partners a great reason to choose to collaborate with us. They need to know who we are, what makes us different/appealing, and who we are looking for to connect with.
The final product should communicate high performance and connectedness.
Updates

Target Market(s)

professional medical allied health and fitness practitioners

Industry/Entity Type

Health

Requirements
Must have
• energetic, vibrant, engaging, inviting, images

```html
<!DOCTYPE html>
<html lang="en">
<head>
<meta charset="utf-8">
<title>Referral Partnerships Booklet</title>
<link href="https://fonts.googleapis.com/css2?family=Cinzel:wght@400;700&family=Montserrat:wght@400;600;700&display=swap" rel="stylesheet">
<style>
:root{
  --bg:#e4e5e7;
  --paper:#ffffff;
  --orange:#f39a1e;
  --red:#c4242f;
  --teal:#20a99a;
  --green:#5cb848;
  --blue:#2a4ea2;
  --navy:#1f3a8f;
  --brown:#a5695c;
  --ink:#3a3a3a;
  --muted:#7b7b7b;
  --pink:#e0489a;
  --violet:#7a4fa3;
}
*{box-sizing:border-box;margin:0;padding:0}
html,body{width:1200px;height:3594px;overflow:hidden;background:var(--bg);font-family:"Montserrat",sans-serif;color:var(--ink)}
.canvas{width:1200px;height:3594px;display:flex;flex-direction:column}
.stage{height:1198px;display:flex;align-items:center;justify-content:center}
.page{position:relative;background:var(--paper);overflow:hidden;box-shadow:0 10px 28px rgba(0,0,0,.16)}
.spread{display:flex;box-shadow:0 12px 30px rgba(0,0,0,.18)}
.spread .page{box-shadow:none;width:560px;height:792px}
.spread .page + .page{border-left:1px solid #ddd}

/* cover (scales with its width) */
.cover{container-type:inline-size}
.stage--cover .cover{width:700px;height:990px}
.cover__title{position:absolute;left:20%;top:9.5%;width:48%;font-family:"Cinzel",serif;font-weight:700;color:var(--red);font-size:5cqw;line-height:1.1;letter-spacing:.03em;text-align:right;white-space:nowrap}
.cover__sub{position:absolute;left:20%;top:19.5%;width:48%;text-align:right;font-size:1.35cqw;color:var(--muted);letter-spacing:.06em;text-transform:uppercase}
.cover__tab{position:absolute;left:70%;top:10%;width:30%;height:12%;background:var(--orange);padding:2.4cqw 2.6cqw;color:#fff;font-size:1.7cqw;line-height:1.45;text-transform:uppercase;letter-spacing:.04em}
.cover__mosaic{position:absolute;left:16%;top:24%;width:60%;height:54%}
.cover__cta{position:absolute;left:44%;top:80%;width:40%;font-size:2.1cqw;line-height:1.35;color:var(--blue);text-transform:uppercase;letter-spacing:.06em}

/* shared */
.tab{position:absolute;background:var(--orange);color:#fff;font-family:"Cinzel",serif;font-weight:700;font-size:13px;letter-spacing:.08em;padding:7px 14px;text-transform:uppercase}
.photo{position:absolute}
.small{font-size:7.5px;line-height:1.5}

/* about page */
.values-copy{position:absolute;left:230px;top:30px;width:195px}
.values-copy b{color:var(--ink);text-transform:uppercase}
.values-hex{position:absolute;left:430px;top:30px;width:120px;height:180px}
.about-tab{left:0;top:222px;width:180px;text-align:right}
.about-photo{left:26px;top:252px;width:478px;height:300px;background:linear-gradient(135deg,#d9dde0,#f1efed 45%,#c9b7ab)}
.about-caption{position:absolute;left:318px;top:474px;width:186px;height:78px;background:var(--brown);color:#fff;font-size:9px;line-height:1.45;padding:12px 14px;text-align:center}
.love{position:absolute;left:26px;top:572px;width:230px}
.love__intro{font-size:8px;line-height:1.5;margin-bottom:10px}
.love__list{list-style:none}
.love__list li{position:relative;padding-left:20px;font-size:7.5px;line-height:1.5;margin-bottom:10px}
.love__list li::before{content:"";position:absolute;left:2px;top:3px;width:8px;height:8px;background:var(--teal);transform:rotate(45deg)}
.team{position:absolute;left:270px;top:586px;width:280px}
.team__title{font-family:"Cinzel",serif;color:var(--teal);font-size:16px;letter-spacing:.1em;text-align:center;margin-bottom:8px}
.team__row{display:flex;justify-content:space-between}
.member{width:52px;text-align:center}
.member svg{width:52px;height:58px;display:block}
.member p{font-size:5.5px;line-height:1.35;margin-top:4px}

/* way page */
.way-title{position:absolute;left:40px;top:52px;width:210px;font-family:"Cinzel",serif;font-size:15px;line-height:1.2;text-align:center;letter-spacing:.04em}
.way-copy{position:absolute;left:40px;top:100px;width:210px;font-size:8px;line-height:1.55}
.way-collage{position:absolute;left:22px;top:218px;width:236px;height:490px;display:grid;grid-template-columns:1fr 1fr;grid-template-rows:1fr 1fr 1fr;gap:4px}
.way-collage div:nth-child(1){grid-column:1/3;background:linear-gradient(135deg,#7a5a4a,#c99a7a)}
.way-collage div:nth-child(2){background:linear-gradient(135deg,#5a4036,#9a6f58)}
.way-collage div:nth-child(3){background:linear-gradient(135deg,#8a6b56,#c7a68a)}
.way-collage div:nth-child(4){background:linear-gradient(135deg,#6b5246,#a9876f)}
.way-collage div:nth-child(5){background:linear-gradient(135deg,#9a7862,#d3b597)}
.fix-tab{left:296px;top:18px;width:264px;padding:9px 18px;text-align:center}
.steps{position:absolute;left:300px;top:66px;width:245px;list-style:none}
.step{display:grid;grid-template-columns:24px 1fr;column-gap:6px;margin-bottom:13px}
.step__num{font-family:"Cinzel",serif;font-size:16px;line-height:1}
.step__name{font-family:"Cinzel",serif;font-size:7.5px;text-transform:uppercase;letter-spacing:.04em;padding-top:4px}
.step__note{font-size:5.5px;color:var(--muted)}
.step ul{grid-column:2;list-style:none;margin-top:3px}
.step li{position:relative;padding-left:11px;font-size:6.5px;line-height:1.55}
.step li::before{content:"";position:absolute;left:1px;top:3px;width:5px;height:5px;background:var(--teal);transform:rotate(45deg)}

/* back page */
.partners-tab{position:absolute;left:26px;top:120px;width:220px;background:var(--blue);color:#fff;font-size:9px;letter-spacing:.1em;text-transform:uppercase;padding:6px 12px}
.partners-grid{position:absolute;left:26px;top:152px;width:220px;display:grid;grid-template-columns:1fr 1fr;gap:16px 14px}
.partner{display:flex;align-items:center;gap:6px}
.partner i{width:20px;height:20px;border-radius:50%;flex:none}
.partner span{font-size:7px;line-height:1.3;color:var(--ink)}
.back-photo{left:270px;top:120px;width:230px;height:150px;background:linear-gradient(135deg,#b7c9b4,#e6e2da 50%,#7c9ad0)}
.required{position:absolute;left:270px;top:290px;width:230px;text-align:center}
.required h3{font-family:"Cinzel",serif;font-size:9px;letter-spacing:.08em;margin-bottom:12px}
.required__grid{display:grid;grid-template-columns:repeat(3,1fr);gap:12px 6px}
.required__grid div{font-size:5.5px;line-height:1.3;color:var(--muted)}
.required__grid i{display:block;width:22px;height:22px;border-radius:50%;margin:0 auto 4px}
.overview{position:absolute;left:150px;top:470px;width:170px;height:120px;background:var(--navy);color:#fff;font-size:7px;line-height:1.4;padding:70px 14px 0;text-align:right;text-transform:uppercase;letter-spacing:.05em}
.logos{position:absolute;left:30px;top:640px;width:460px;display:flex;justify-content:space-between;align-items:center}
.logos i{display:block;width:38px;height:24px;background:#d6d9de}
.logos i:nth-child(odd){border-radius:50%;width:28px;height:28px}
</style>
</head>
<body>
<main class="canvas">

  <!-- Front cover -->
  <section class="stage stage--cover">
    <article class="page cover">
      <h1 class="cover__title">Referral<br>Partnerships</h1>
      <p class="cover__sub">Because together we can achieve more</p>
      <div class="cover__tab"><p>We are here to partner with you and your clients</p></div>
      <svg class="cover__mosaic" viewBox="0 0 400 500" role="img" aria-label="Colourful triangle mosaic framing photos of hands joined in teamwork and a practitioner treating a patient's feet">
        <defs>
          <linearGradient id="mosaicFill" x1="0" y1="0" x2="1" y2="1">
            <stop offset="0" stop-color="#e0489a"/>
            <stop offset=".3" stop-color="#2a4ea2"/>
            <stop offset=".55" stop-color="#c4242f"/>
            <stop offset=".8" stop-color="#5cb848"/>
            <stop offset="1" stop-color="#d8c8d8"/>
          </linearGradient>
        </defs>
        <polygon points="200,0 400,120 400,360 200,500 0,360 0,120" fill="url(#mosaicFill)" opacity=".88"/>
      </svg>
      <p class="cover__cta">Let's combine our skillsets so we can achieve even better results</p>
    </article>
  </section>

  <!-- Inside spread -->
  <section class="stage">
    <div class="spread">
      <article class="page about">
        <div class="values-copy small">
          <p><b>Courage</b> gives us the strength and confidence to take risks and embrace challenges. <b>Inspiration</b> is our energy; we fuel it in our work. <b>Fun</b> is the force that holds us as one and drives us forward every day. <b>Creativity</b> keeps us fresh and open to ideas. <b>Wow</b> means we go beyond what is expected for every client who walks in. <b>Team</b> is who we are; every person brings their best and we grow by supporting each other.</p>
        </div>
        <svg class="values-hex" viewBox="0 0 120 180" aria-label="Our values">
          <g font-family="Montserrat, sans-serif" font-size="5.5" text-anchor="middle">
            <polygon points="30,8 48,18 48,38 30,48 12,38 12,18" fill="none" stroke="#5cb848"/><text x="30" y="30" fill="#3a3a3a">COURAGE</text>
            <polygon points="70,8 88,18 88,38 70,48 52,38 52,18" fill="#5cb848"/><text x="70" y="30" fill="#fff">INSPIRE</text>
            <polygon points="50,44 68,54 68,74 50,84 32,74 32,54" fill="#5cb848"/><text x="50" y="66" fill="#fff">CREATIVE</text>
            <polygon points="90,44 108,54 108,74 90,84 72,74 72,54" fill="none" stroke="#5cb848"/><text x="90" y="66" fill="#3a3a3a">FUN</text>
            <polygon points="70,80 88,90 88,110 70,120 52,110 52,90" fill="none" stroke="#5cb848"/><text x="70" y="102" fill="#3a3a3a">WOW</text>
            <polygon points="50,116 68,126 68,146 50,156 32,146 32,126" fill="#5cb848"/><text x="50" y="138" fill="#fff">TEAM</text>
          </g>
        </svg>
        <h2 class="tab about-tab">About Us</h2>
        <div class="photo about-photo" role="img" aria-label="Photo of a practitioner in a white coat treating the foot of a smiling patient on a clinic bed"></div>
        <p class="about-caption">At The Linden Practice we are passionate about building strong postural foundations from the feet up.</p>
        <div class="love">
          <p class="love__intro">The top 3 things our clients love about us (and hopefully yours will too!)</p>
          <ul class="love__list">
            <li>Positive energy, enthusiasm and our clients' NPS average score of 9 out of 10.</li>
            <li>Trusted leader in the practice of podiatric medicine established 2006, also experience, latest high-tech equipment.</li>
            <li>Focus is on strong feet, not just orthotics; Stride Institute Technology, Fascia Pathways, Foot Mobility Therapist.</li>
          </ul>
        </div>
        <div class="team">
          <h3 class="team__title">Our Team</h3>
          <div class="team__row">
            <div class="member"><svg viewBox="0 0 52 58" role="img" aria-label="Portrait of a team member"><polygon points="26,1 51,15 51,43 26,57 1,43 1,15" fill="#b89a86" stroke="#20a99a" stroke-width="2"/></svg><p>Dr Lena Hart<br>Principal Podiatrist</p></div>
            <div class="member"><svg viewBox="0 0 52 58" role="img" aria-label="Portrait of a team member"><polygon points="26,1 51,15 51,43 26,57 1,43 1,15" fill="#a98872" stroke="#c4242f" stroke-width="2"/></svg><p>Dr Owen Pike<br>Podiatrist</p></div>
            <div class="member"><svg viewBox="0 0 52 58" role="img" aria-label="Portrait of a team member"><polygon points="26,1 51,15 51,43 26,57 1,43 1,15" fill="#c2a48e" stroke="#20a99a" stroke-width="2"/></svg><p>Dr Mia Cole<br>Podiatrist</p></div>
            <div class="member"><svg viewBox="0 0 52 58" role="img" aria-label="Portrait of a team member"><polygon points="26,1 51,15 51,43 26,57 1,43 1,15" fill="#9c7c68" stroke="#c4242f" stroke-width="2"/></svg><p>Ava Reid<br>Practice Manager</p></div>
            <div class="member"><svg viewBox="0 0 52 58" role="img" aria-label="Portrait of a team member"><polygon points="26,1 51,15 51,43 26,57 1,43 1,15" fill="#b5937c" stroke="#20a99a" stroke-width="2"/></svg><p>Zoe Lund<br>Client Officer</p></div>
          </div>
        </div>
      </article>

      <article class="page way">
        <h2 class="way-title">The<br>Linden Practice Way</h2>
        <p class="way-copy">Our pathway to strengthen postural foundations, to create lasting change, to free up movement, and ultimately keep us going well beyond what we thought was possible (updated as research and tech changes).</p>
        <div class="way-collage" role="img" aria-label="Collage of photos of the clinic team, group classes and clients training barefoot">
          <div></div><div></div><div></div><div></div><div></div>
        </div>
        <h2 class="tab fix-tab">Fix Your Feet</h2>
        <ol class="steps">
          <li class="step"><span class="step__num">01</span><span class="step__name">Fix the pain</span>
            <ul><li>Provide analgesia</li><li>Reduce inflammation</li><li>Correct or offload foot loading</li><li>Improve thickened tissue repair and maintenance</li><li>Surgery</li></ul></li>
          <li class="step"><span class="step__num">02</span><span class="step__name">Protect the feet <span class="step__note">(reduce damage, optimise stability)</span></span>
            <ul><li>Reduce tissue damage</li><li>Optimise foot posture</li><li>Activate neuromuscular balance and stability</li><li>Promote tissue repair and regeneration</li></ul></li>
          <li class="step"><span class="step__num">03</span><span class="step__name">Strengthen the feet <span class="step__note">(improve strength and endurance)</span></span>
            <ul><li>Strengthen toe muscles</li><li>Connect foot strength to core strength</li><li>Stimulate neuromuscular strength</li><li>Refresh your body</li></ul></li>
          <li class="step"><span class="step__num">04</span><span class="step__name">Protect the whole body <span class="step__note">(stability)</span></span>
            <ul><li>Optimise postural alignment</li><li>Activate neuromuscular balance and stability</li><li>Customised corrective exercises</li><li>Improve cellular regeneration</li><li>Optimise nutrition and healthy gut</li><li>Optimise healthy mind</li></ul></li>
          <li class="step"><span class="step__num">05</span><span class="step__name">Strengthen the whole body <span class="step__note">(strength, elasticity)</span></span>
            <ul><li>Strengthen the deep core (stabilisers)</li><li>Strengthen the outer core (mobilisers)</li><li>Increase fascial elasticity and strength</li><li>Increase functional strength</li><li>Increase endurance</li><li>Customised nutrition for performance</li><li>Improve psychological resilience</li></ul></li>
          <li class="step"><span class="step__num">06</span><span class="step__name">Repeat consistently</span></li>
        </ol>
      </article>
    </div>
  </section>

  <!-- Back and front cover spread -->
  <section class="stage">
    <div class="spread">
      <article class="page back">
        <h2 class="partners-tab">Our trusted partners</h2>
        <div class="partners-grid">
          <div class="partner"><i style="background:var(--blue)"></i><span>Harbour Sports Medicine</span></div>
          <div class="partner"><i style="background:var(--orange)"></i><span>Northgate Physio</span></div>
          <div class="partner"><i style="background:var(--red)"></i><span>Keel Fitness Co</span></div>
          <div class="partner"><i style="background:var(--green)"></i><span>Tallow Pilates</span></div>
          <div class="partner"><i style="background:var(--teal)"></i><span>Bayline Chiro</span></div>
          <div class="partner"><i style="background:var(--violet)"></i><span>Crest Run Club</span></div>
        </div>
        <div class="photo back-photo" role="img" aria-label="Photo of a runner's legs and shoes mid-stride outdoors"></div>
        <div class="required">
          <h3>Referral partners required</h3>
          <div class="required__grid">
            <div><i style="background:var(--blue)"></i>GPs</div>
            <div><i style="background:var(--pink)"></i>Physios</div>
            <div><i style="background:var(--orange)"></i>Chiros</div>
            <div><i style="background:var(--teal)"></i>Personal trainers</div>
            <div><i style="background:var(--violet)"></i>Pilates studios</div>
            <div><i style="background:var(--green)"></i>Sports clubs</div>
            <div><i style="background:var(--red)"></i>Massage</div>
            <div><i style="background:var(--orange)"></i>Yoga</div>
            <div><i style="background:var(--blue)"></i>Dietitians</div>
          </div>
        </div>
        <div class="overview"><p>Our business at a glance</p></div>
        <div class="logos" aria-label="Memberships and accreditations"><i></i><i></i><i></i><i></i><i></i><i></i><i></i></div>
      </article>
      <article class="page cover">
        <h1 class="cover__title">Referral<br>Partnerships</h1>
        <p class="cover__sub">Because together we can achieve more</p>
        <div class="cover__tab"><p>We are here to partner with you and your clients</p></div>
        <svg class="cover__mosaic" viewBox="0 0 400 500" role="img" aria-label="Colourful triangle mosaic framing photos of hands joined in teamwork and a practitioner treating a patient's feet">
          <polygon points="200,0 400,120 400,360 200,500 0,360 0,120" fill="url(#mosaicFill)" opacity=".88"/>
        </svg>
        <p class="cover__cta">Let's combine our skillsets so we can achieve even better results</p>
      </article>
    </div>
  </section>

</main>
</body>
</html>
```